Web Developer Needs a Business Card Design

I need a personal business card design that represents me as a web developer for potential employers. I would like the background to be a dark color on the front for contrast with my logo and name. The back will have all my information along with a smaller version of the logo. I want something with a modern look and feel, not too conservative. This will be used for potential employers and freelance work.

Industry/Entity Type

Business

Contact Information for Business Card

Front should have my logo and name. The back should have all my personal information which would include: name: Tom Varulek, phone: 570-614-3098, email: tomvarulek@quillbox.net, website url: www.tomvarulek.net, logo, web developer.

Font styles to use
Sans Serif

Requirements
Must have
• Must include my logo. The color palette base color will be the logo color.

```html
<!DOCTYPE html>
<html lang="en">
<head>
<meta charset="utf-8">
<title>Tom Varulek — Business Card</title>
<link href="https://fonts.googleapis.com/css2?family=Source+Sans+3:wght@400;600;700&display=swap" rel="stylesheet">
<style>
  :root {
    --backdrop: #151515;
    --teal: #6dc7b4;
    --white: #ffffff;
    --ink-grey: #6b6b6b;
  }
  * { margin: 0; padding: 0; box-sizing: border-box; }
  html, body {
    width: 1200px; height: 900px; overflow: hidden;
    background: var(--backdrop);
    font-family: "Source Sans 3", "Helvetica Neue", Arial, sans-serif;
  }
  .stage { position: relative; width: 1200px; height: 900px; }
  .card {
    position: absolute; top: 170px; width: 347px; height: 561px;
    box-shadow: 0 4px 14px rgba(0,0,0,.45);
  }
  .card--info { left: 259px; background: var(--white); }
  .card--front { left: 631px; background: var(--teal); }

  .band { position: absolute; left: 102px; width: 143px; background: var(--teal); }
  .band--top { top: 0; height: 30px; }
  .band--bottom { bottom: 0; height: 28px; }

  .mark { position: absolute; display: flex; align-items: center; justify-content: center; border-radius: 50%; }
  .card--info .mark {
    left: 70px; top: 98px; width: 208px; height: 208px;
    border: 13px solid var(--teal);
  }
  .card--front .mark {
    left: 34px; top: 141px; width: 280px; height: 280px;
    border: 17px solid var(--white);
  }
  .mark__name { font-weight: 700; letter-spacing: .5px; }
  .card--info .mark__name { color: var(--teal); font-size: 34px; }
  .card--front .mark__name { color: var(--white); font-size: 46px; }

  .identity { position: absolute; left: 0; right: 0; top: 333px; text-align: center; }
  .identity__name { color: var(--teal); font-size: 19px; font-weight: 700; line-height: 24px; }
  .identity__role { color: var(--ink-grey); font-size: 15.5px; line-height: 22px; }

  .contacts { position: absolute; left: 0; right: 0; top: 399px; list-style: none; text-align: center; }
  .contacts li {
    color: var(--ink-grey); font-size: 15.5px; line-height: 20.5px;
    display: flex; align-items: center; justify-content: center; gap: 7px;
  }
  .contacts svg { width: 10px; height: 10px; fill: var(--teal); flex: none; }

  .front-name {
    position: absolute; left: 0; right: 0; top: 457px; text-align: center;
    color: var(--white); font-size: 27px; font-weight: 700;
  }
</style>
</head>
<body>
<main class="stage">
  <section class="card card--info" aria-label="Card back with contact details">
    <div class="band band--top"></div>
    <div class="mark"><span class="mark__name">Varulek</span></div>
    <div class="identity">
      <p class="identity__name">Tom Varulek</p>
      <p class="identity__role">Front-End Developer</p>
    </div>
    <ul class="contacts">
      <li>
        <svg viewBox="0 0 10 10" aria-hidden="true"><path d="M2 0.5 3.6 2.6 2.8 3.7C3.4 5 4.9 6.6 6.3 7.2L7.4 6.4 9.5 8 8.6 9.4C4.5 9.4.6 5.5.6 1.4Z"/></svg>
        570-614-3098
      </li>
      <li>
        <svg viewBox="0 0 10 10" aria-hidden="true"><path d="M0 2h10v6H0z M0 2l5 3.4L10 2" stroke="#fff" stroke-width=".8"/></svg>
        tomvarulek@quillbox.net
      </li>
      <li>
        <svg viewBox="0 0 10 10" aria-hidden="true"><circle cx="5" cy="5" r="4.8"/><path d="M.5 5h9M5 .3v9.4M5 .3C2.8 3 2.8 7 5 9.7M5 .3C7.2 3 7.2 7 5 9.7" stroke="#fff" stroke-width=".7" fill="none"/></svg>
        www.tomvarulek.net
      </li>
    </ul>
    <div class="band band--bottom"></div>
  </section>

  <section class="card card--front" aria-label="Card front">
    <div class="mark"><span class="mark__name">Varulek</span></div>
    <p class="front-name">Tom Varulek</p>
  </section>
</main>
</body>
</html>
```